Road Construction Company needs business cards

We would like a new business card designed for our business.

We're a road construction company based in Qld, Australia.

Can the business card please have the following information on it.

Name: Warren Halbeck
Position: General Manager
Phone: 0472 915 348
Email: Warren.halbeck@tovrin.com.au
Address: 87 Marrow Ave, Pendlebay, QLD, 4023
Website: www.tovrin.com.au

Visually we'd like the card to be professional and simple.

Attached is our logo.

Our website is www.tovrin.com.au

Target Market(s)

Men aged 25-60

Contact Information for Business Card

As listed in project description

Font styles to use
Serif

Requirements
Must have
• Large logo on back of card

```html
<!DOCTYPE html>
<html lang="en">
<head>
<meta charset="utf-8">
<title>Tovrin Business Card</title>
<link href="https://fonts.googleapis.com/css2?family=Belleza&display=swap" rel="stylesheet">
<style>
  :root {
    --stage: #e9ebee;
    --card-white: #ffffff;
    --card-grey: #ececec;
    --card-blue: #b9d6ee;
    --brand-navy: #0d4f9a;
    --brand-sky: #3a9ad6;
    --text-grey: #4a4a4a;
  }
  * { box-sizing: border-box; margin: 0; padding: 0; }
  html, body { width: 1200px; height: 900px; overflow: hidden; }
  body {
    background: var(--stage);
    font-family: "Belleza", sans-serif;
    position: relative;
  }
  .card {
    position: absolute;
    left: 290px;
    width: 620px;
    height: 354px;
    border-radius: 30px;
    overflow: hidden;
    box-shadow: 0 10px 28px rgba(0,0,0,0.18);
  }
  .card--back {
    top: 74px;
    background:
      radial-gradient(ellipse at 50% 50%, var(--card-white) 0%, #f3f5f8 45%, rgba(255,255,255,0) 75%),
      linear-gradient(135deg, var(--card-blue) 0%, #eef3f8 40%, #eef3f8 60%, var(--card-blue) 100%);
  }
  .card--front {
    top: 472px;
    background: linear-gradient(160deg, var(--card-white) 0%, var(--card-white) 50%, var(--card-grey) 100%);
  }
  .brand {
    display: flex;
    align-items: center;
    gap: 14px;
    color: var(--brand-navy);
    font-family: "Belleza", sans-serif;
    letter-spacing: 0.06em;
  }
  .brand__mark {
    width: 14px; height: 14px;
    background: var(--brand-sky);
  }
  .card--back .brand {
    position: absolute;
    left: 50%; top: 50%;
    transform: translate(-50%, -50%);
    font-size: 64px;
  }
  .card--back .brand__mark { width: 22px; height: 22px; }
  .card--front .brand {
    position: absolute;
    left: 28px; top: 30px;
    font-size: 40px;
  }
  .person {
    position: absolute;
    right: 332px;
    top: 236px;
    text-align: right;
  }
  .person__role { color: var(--text-grey); font-size: 17px; }
  .person__name { color: var(--brand-navy); font-size: 20px; letter-spacing: 0.02em; margin-top: 2px; }
  .divider {
    position: absolute;
    left: 302px; top: 150px;
    width: 1.5px; height: 150px;
    background: var(--brand-sky);
  }
  .contacts {
    position: absolute;
    left: 322px; top: 156px;
    list-style: none;
    color: var(--text-grey);
    font-size: 17px;
  }
  .contacts li {
    display: flex;
    align-items: flex-start;
    gap: 10px;
    line-height: 1.55;
  }
  .contacts svg { width: 14px; height: 14px; margin-top: 5px; flex-shrink: 0; fill: var(--brand-navy); }
</style>
</head>
<body>

<section class="card card--back" aria-label="Card back">
  <div class="brand"><span class="brand__mark"></span>TOVRIN</div>
</section>

<section class="card card--front" aria-label="Card front">
  <div class="brand"><span class="brand__mark"></span>TOVRIN</div>

  <div class="person">
    <p class="person__role">General Manager</p>
    <p class="person__name">WARREN HALBECK</p>
  </div>

  <div class="divider"></div>

  <ul class="contacts">
    <li>
      <svg viewBox="0 0 24 24"><path d="M6.6 10.8a15.1 15.1 0 0 0 6.6 6.6l2.2-2.2c.3-.3.7-.4 1-.2 1.1.4 2.3.6 3.6.6.6 0 1 .4 1 1V20c0 .6-.4 1-1 1C10.6 21 3 13.4 3 4c0-.6.4-1 1-1h3.5c.6 0 1 .4 1 1 0 1.3.2 2.5.6 3.6.1.3 0 .7-.2 1z"/></svg>
      <span>0472 915 348</span>
    </li>
    <li>
      <svg viewBox="0 0 24 24"><path d="M12 2a10 10 0 1 0 0 20 10 10 0 0 0 0-20zm6.9 6h-3a15.7 15.7 0 0 0-1.3-3.6A8 8 0 0 1 18.9 8zM12 4c.8 1.2 1.5 2.5 1.9 4h-3.8c.4-1.5 1.1-2.8 1.9-4zM4.3 14a8 8 0 0 1 0-4h3.4a16 16 0 0 0 0 4zm.8 2h3a15.7 15.7 0 0 0 1.3 3.6A8 8 0 0 1 5.1 16zm3-8h-3a8 8 0 0 1 4.3-3.6C8.8 5.5 8.4 6.7 8.1 8zM12 20c-.8-1.2-1.5-2.5-1.9-4h3.8c-.4 1.5-1.1 2.8-1.9 4zm2.3-6H9.7a14.7 14.7 0 0 1 0-4h4.6a14.7 14.7 0 0 1 0 4zm.3 5.6c.6-1.1 1-2.3 1.3-3.6h3a8 8 0 0 1-4.3 3.6zm1.7-5.6a16 16 0 0 0 0-4h3.4a8 8 0 0 1 0 4z"/></svg>
      <span>www.tovrin.com.au</span>
    </li>
    <li>
      <svg viewBox="0 0 24 24"><path d="M3 5h18a1 1 0 0 1 1 1v12a1 1 0 0 1-1 1H3a1 1 0 0 1-1-1V6a1 1 0 0 1 1-1zm9 7.5L20 7H4z"/></svg>
      <span>Warren.halbeck@tovrin.com.au</span>
    </li>
    <li>
      <svg viewBox="0 0 24 24"><path d="M12 2a7 7 0 0 0-7 7c0 5.2 7 13 7 13s7-7.8 7-13a7 7 0 0 0-7-7zm0 9.5a2.5 2.5 0 1 1 0-5 2.5 2.5 0 0 1 0 5z"/></svg>
      <span>87 Marrow Ave<br>Pendlebay, QLD, 4023</span>
    </li>
  </ul>
</section>

</body>
</html>
```